Tavenhurst Falcons FC Website

We are looking to develop a new website for Tavenhurst FC. Tavenhurst FC has now joined with Tavenhurst Falcons FC and we are looking at a website that can work for both clubs. Tavenhurst FC play in a local park football competition while tavenhurst Falcons are a Semi Professional team that plays in the Ostral Premier Series Competition. What we are after is two separate website off the one platform. I have attached both team logos for you to visualise. Also you can look at the existing tavenhurst website www.tavenhurstfc.net.au. We are looking for a huge improvement in the website and it will be imperative we have links to sponsors and the sponsors can get regular visuals. Weare looking to move this club forward and have a very professional website that can communicate clearly with the community.

Hi All,

Please remember that the website is to represent two clubs;
1. Tavenhurst Falcons FC (Competes in Semi Professional League)
2. Tavenhurst FC (Compete in KPWLT League which is a lower level)

Further to this the Tavenhurst Falcons FC page will require a player profile page which will show photos of each player and a little bio on each.

Thanks

Reason: Would like to spend more time review existing and new designs

```html
<!DOCTYPE html>
<html lang="en">
<head>
<meta charset="utf-8">
<title>Tavenhurst Falcons FC</title>
<link href="https://fonts.googleapis.com/css2?family=Crimson+Text:wght@400;600;700&family=Arimo:wght@400;700&display=swap" rel="stylesheet">
<style>
:root{
  --red:#d10a11;
  --red-dark:#a5070c;
  --ink:#222;
  --text:#555;
  --muted:#777;
  --page:#efefef;
  --white:#fff;
  --rule:#d6d6d6;
}
*{margin:0;padding:0;box-sizing:border-box}
html,body{width:875px;height:1200px;overflow:hidden}
body{position:relative;background:var(--page);font-family:"Crimson Text",serif;color:var(--text)}
.abs{position:absolute}
.header{left:0;top:0;width:875px;height:131px;background:linear-gradient(#fff,#f3f3f3)}
.brand-mark{left:150px;top:18px;width:72px;height:72px;border-radius:50%;background:var(--red)}
.brand-name{left:118px;top:100px;font-size:17px;font-weight:700;color:var(--ink);white-space:nowrap}
.social{top:48px;width:11px;height:11px;border-radius:50%;background:var(--red)}
.register{left:652px;top:42px;width:105px;height:24px;background:var(--red);border:2px solid var(--red);outline:1px solid #fff;outline-offset:-4px;color:#fff;font:400 9.5px "Arimo",sans-serif;text-align:center;line-height:20px}
.nav{top:105px;font:400 9px "Arimo",sans-serif;color:var(--ink);white-space:nowrap}
.nav.active{color:var(--red)}
.caret{width:0;height:0;border-left:3.5px solid transparent;border-right:3.5px solid transparent;border-top:4px solid #999}
.caret.red{border-top-color:var(--red)}
.redline{left:0;top:131px;width:875px;height:2.5px;background:var(--red)}
.hero{left:0;top:133px;width:875px;height:322px;background:radial-gradient(ellipse at 50% 35%,#b9b49a 0%,#8e8b6b 40%,#5f6a3c 75%,#4c5a2a 100%)}
.dropdown{left:623px;top:134px;width:98px;background:var(--red)}
.dropdown div{height:20.5px;line-height:20.5px;text-align:center;color:#fff;font:400 9px/20.5px "Arimo",sans-serif;border-bottom:1px solid #e2474c}
.dropdown div:last-child{border-bottom:0}
.caption{left:346px;top:231px;width:184px;height:26px;background:rgba(40,40,40,.85);color:#fff;font-size:15px;text-align:center;line-height:26px}
.caption b{font-weight:700}
.arrow{top:279px;width:32px;height:31px;background:rgba(40,40,40,.85)}
.card{top:374px;width:192px;height:239px;background:var(--white);border-top:4px solid var(--red);box-shadow:0 10px 8px -8px rgba(0,0,0,.25)}
.card h2{position:absolute;left:0;top:13px;width:100%;text-align:center;font-size:16px;font-weight:600;color:var(--ink)}
.card .photo{position:absolute;left:15px;top:41px;width:162px;height:89px;border:3px solid #eee}
.card p{position:absolute;left:14px;top:148px;width:164px;text-align:center;font-size:9px;line-height:12px;color:var(--text)}
.btn{background:var(--red);color:#fff;text-align:center;font-size:11px;border:1px solid var(--red);outline:1px solid #fff;outline-offset:-3px}
.card .btn{position:absolute;left:71px;top:193px;width:48px;height:22px;line-height:20px}
.section-title{top:646px;font-size:17px;font-weight:600;color:var(--ink)}
.news-thumb{left:118px;width:81px;height:82px;background:#fff;border:1px solid #e3e3e3;padding:3px}
.news-thumb div{width:100%;height:100%}
.news-date{left:215px;font-size:11.5px;color:var(--text)}
.news-text{left:215px;width:285px;font-size:9px;line-height:12px;color:var(--text)}
.more-info{left:215px;font-size:8px;color:var(--red);text-decoration:underline}
.sep{left:118px;width:375px;height:1px;background:var(--rule)}
.divider{left:517px;top:650px;width:1px;height:382px;background:var(--rule)}
.fix-thumb{width:98px;height:98px;background:#fff;border:1px solid #e3e3e3;padding:6px}
.fix-thumb div{width:100%;height:100%}
.fix-label{width:98px;text-align:center;font-size:11px;color:var(--ink)}
.footer{left:0;top:1054px;width:875px;height:146px;background:var(--white);border-top:1px solid #e5e5e5}
.foot-links{left:118px;top:1071px;font:400 8px "Arimo",sans-serif;color:var(--muted);white-space:nowrap}
.foot-links span{color:var(--red)}
.foot-brand{left:118px;top:1118px;font-size:13px;font-weight:700;color:var(--red);display:flex;align-items:center;gap:6px}
.foot-brand i{display:block;width:14px;height:14px;border-radius:50%;background:var(--red)}
.copy{left:118px;top:1167px;font:400 8.5px "Arimo",sans-serif;color:var(--muted)}
.copy u{color:var(--muted)}
.foot-social{top:1171px;width:9px;height:9px;border-radius:50%;background:var(--red)}
.foot-list{list-style:none;font:400 8px "Arimo",sans-serif;color:var(--ink)}
.foot-list li{height:19.2px;position:relative;padding-left:8px}
.foot-list li::before{content:"";position:absolute;left:0;top:3px;width:3px;height:3px;background:var(--red)}
</style>
</head>
<body>
<div class="abs header"></div>
<div class="abs brand-mark"></div>
<div class="abs brand-name">Tavenhurst Falcons FC</div>

<div class="abs social" style="left:568px"></div>
<div class="abs social" style="left:593px"></div>
<div class="abs social" style="left:619px"></div>
<div class="abs register">REGISTER ONLINE</div>

<div class="abs nav" style="left:310px">HOME</div>
<div class="abs nav" style="left:356px">NEWS</div>
<div class="abs nav" style="left:402px">FIXTURE &amp; RESULTS</div>
<div class="abs caret" style="left:441px;top:120px"></div>
<div class="abs nav" style="left:506px">PHOTO GALLERY</div>
<div class="abs nav" style="left:597px">SPONSOR</div>
<div class="abs nav active" style="left:660px">CLUB</div>
<div class="abs caret red" style="left:668px;top:120px"></div>
<div class="abs nav" style="left:705px">CONTACT US</div>
<div class="abs redline"></div>

<div class="abs hero" role="img" aria-label="Action photo of a footballer kicking the ball past a diving goalkeeper on a grass pitch"></div>
<div class="abs caption">The <b>Game</b> Is About <b>Glory</b></div>
<div class="abs arrow" style="left:35px"><svg width="32" height="31"><path d="M19 8 L12 15.5 L19 23" stroke="#fff" stroke-width="2" fill="none"/></svg></div>
<div class="abs arrow" style="left:802px"><svg width="32" height="31"><path d="M13 8 L20 15.5 L13 23" stroke="#fff" stroke-width="2" fill="none"/></svg></div>
<div class="abs dropdown">
  <div>History</div><div>Management</div><div>Awards</div><div>Registration</div>
</div>

<div class="abs card" style="left:118px">
  <h2>News Headlines</h2>
  <div class="photo" role="img" aria-label="Young players seated on the grass with their coach" style="background:linear-gradient(#8fae6a,#5f8a3c)"></div>
  <p>Lorem ipsum dolor sit amet, consectetur adipisicing elit, sed do eiusmod tempor incididunt ...</p>
  <div class="btn">more</div>
</div>
<div class="abs card" style="left:342px">
  <h2>Our Mission</h2>
  <div class="photo" role="img" aria-label="Club trophy shield on display" style="background:linear-gradient(#8a5a3a,#5a3522)"></div>
  <p>Lorem ipsum dolor sit amet, consectetur adipisicing elit, sed do eiusmod tempor incididunt ut labore et ...</p>
  <div class="btn">more</div>
</div>
<div class="abs card" style="left:566px">
  <h2>Sponsors</h2>
  <div class="photo" role="img" aria-label="Sponsors standing together at a club presentation night" style="background:linear-gradient(#9a9088,#4a423c)"></div>
  <p>Lorem ipsum dolor sit amet, consectetur adipisicing elit, sed do eiusmod tempor incididunt ut ...</p>
  <div class="btn">more</div>
</div>

<div class="abs section-title" style="left:118px">Latest News Updates !</div>

<div class="abs news-thumb" style="top:686px"><div role="img" aria-label="Club officials signing a document" style="background:linear-gradient(#c0a27a,#6a3a2e)"></div></div>
<div class="abs news-date" style="top:686px">18 Mar</div>
<div class="abs news-text" style="top:708px">Lorem ipsum dolor sit amet, consectetur adipisicing elit, sed do eiusmod tempor incididunt ut labore et dolore magna aliqua. Ut enim ad minim veniam, quis nostrud exercitation ullamco ...</div>
<div class="abs more-info" style="top:758px">MORE INFO</div>
<div class="abs sep" style="top:781px"></div>

<div class="abs news-thumb" style="top:795px"><div role="img" aria-label="Club members posing outdoors" style="background:linear-gradient(#9ab0c8,#5a5a3a)"></div></div>
<div class="abs news-date" style="top:795px">5 Mar</div>
<div class="abs news-text" style="top:817px">Lorem ipsum dolor sit amet, consectetur adipisicing elit, sed do eiusmod tempor incididunt ut labore et dolore magna aliqua. Ut enim ad minim veniam, quis nostrud exercitation ullamco ...</div>
<div class="abs more-info" style="top:867px">MORE INFO</div>
<div class="abs sep" style="top:891px"></div>

<div class="abs news-thumb" style="top:904px"><div role="img" aria-label="Award presentation with framed certificate" style="background:linear-gradient(#b08a6a,#3a2e2a)"></div></div>
<div class="abs news-date" style="top:904px">22 Feb</div>
<div class="abs news-text" style="top:926px">Lorem ipsum dolor sit amet, consectetur adipisicing elit, sed do eiusmod tempor incididunt ut labore et dolore magna aliqua. Ut enim ad minim veniam, quis nostrud exercitation ullamco ...</div>
<div class="abs more-info" style="top:976px">MORE INFO</div>

<div class="abs btn" style="left:118px;top:1010px;width:66px;height:21px;line-height:19px">read more</div>

<div class="abs divider"></div>

<div class="abs section-title" style="left:541px">Fixture &amp; Results</div>
<div class="abs fix-thumb" style="left:541px;top:686px"><div role="img" aria-label="Player in red kicking a ball" style="background:linear-gradient(#c8c8c0,#6a8a4a)"></div></div>
<div class="abs fix-thumb" style="left:660px;top:686px"><div role="img" aria-label="Goalkeeper in yellow clearing the ball" style="background:linear-gradient(#6a9a4a,#3a6a2a)"></div></div>
<div class="abs fix-label" style="left:541px;top:791px">Premier League</div>
<div class="abs fix-label" style="left:660px;top:791px">Super League</div>
<div class="abs fix-thumb" style="left:541px;top:826px"><div role="img" aria-label="Player celebrating on the pitch" style="background:linear-gradient(#4a9a4a,#2a6a2a)"></div></div>
<div class="abs fix-thumb" style="left:660px;top:826px"><div role="img" aria-label="Two players contesting the ball" style="background:linear-gradient(#3a6a2a,#5a8a3a)"></div></div>
<div class="abs fix-label" style="left:541px;top:931px">Under 16 / 2</div>
<div class="abs fix-label" style="left:660px;top:931px">Under 17 / 1</div>
<div class="abs btn" style="left:541px;top:977px;width:53px;height:21px;line-height:19px">more</div>

<div class="abs footer"></div>
<div class="abs foot-links"><span>Home</span> &nbsp;| &nbsp;News &nbsp;| &nbsp;Fixture &amp; Results &nbsp;| &nbsp;Photo Gallery &nbsp;| &nbsp;Sponsor &nbsp;| &nbsp;Club &nbsp;| &nbsp;Contact Us</div>
<div class="abs foot-brand"><i></i>Tavenhurst FC</div>
<div class="abs copy">© 2014 &nbsp;| &nbsp;<u>Privacy Policy</u></div>
<div class="abs foot-social" style="left:236px"></div>
<div class="abs foot-social" style="left:255px"></div>
<div class="abs foot-social" style="left:274px"></div>

<ul class="abs foot-list" style="left:561px;top:1073px">
  <li>News</li><li>Tournaments</li><li>Teams</li><li>Training</li><li>Equipment</li><li>Recruiting</li>
</ul>
<ul class="abs foot-list" style="left:682px;top:1073px">
  <li>Recruiting Camps</li><li>Services</li><li>Calendar</li><li>Clinics</li><li>Photo Album</li><li>Our Sponsors</li>
</ul>
</body>
</html>
```